Young, modern, highly skilled carpenter needs business card design

I need a business card design for my construction business. Its called 'Barlow Construction Services'. Im looking for a ultra modern design that incorporates B C S, the first letters of the name with only a subtle reference to carpentry. The design should reflect my high quality work and eye for detail. i have also uploaded some exmaple designs i like.

Industry/Entity Type

Construction

Requirements
Must have
• Name of business, my name, mobile number, ABN number, email address
Nice to have
• A logo incorporating the name of the business

```html
<!DOCTYPE html>
<html lang="en">
<head>
<meta charset="utf-8">
<title>Barlow Construction Services – Business Card</title>
<link rel="stylesheet" href="https://fonts.googleapis.com/css2?family=Carlito:wght@400;700&display=swap">
<style>
  :root {
    --backdrop: #7f8f8e;
    --card-white: #ffffff;
    --brand-green: #4dff00;
    --ink-dark: #1c1c1c;
    --ink-light: #ffffff;
  }
  html, body {
    margin: 0;
    padding: 0;
    overflow: hidden;
  }
  body {
    width: 1200px;
    height: 900px;
    background: var(--backdrop);
    position: relative;
    font-family: "Carlito", "Calibri", sans-serif;
  }
  .card {
    position: absolute;
    box-sizing: border-box;
  }
  .card--front {
    left: 334px;
    top: 62px;
    width: 539px;
    height: 368px;
    background: var(--card-white);
  }
  .card--back {
    left: 334px;
    top: 460px;
    width: 542px;
    height: 372px;
    background: var(--brand-green);
  }
  .brand-mark {
    position: absolute;
    display: flex;
    align-items: center;
    gap: 10px;
    font-weight: 700;
    line-height: 1;
    letter-spacing: 4px;
  }
  .brand-mark__square {
    display: block;
    background: currentColor;
  }
  .card--front .brand-mark {
    left: 54px;
    top: 262px;
    font-size: 66px;
    color: var(--brand-green);
  }
  .card--front .brand-mark__square {
    width: 14px;
    height: 14px;
    background: var(--ink-dark);
  }
  .card--back .brand-mark {
    right: 68px;
    top: 254px;
    font-size: 48px;
    color: var(--ink-light);
  }
  .card--back .brand-mark__square {
    width: 10px;
    height: 10px;
    background: var(--ink-dark);
  }
  .contact {
    position: absolute;
    left: 68px;
    top: 52px;
    margin: 0;
    font-size: 21px;
    line-height: 26px;
    color: var(--ink-dark);
  }
  .contact__name {
    color: var(--ink-light);
    display: block;
  }
  .contact__line {
    display: block;
  }
  .company-name {
    position: absolute;
    left: 66px;
    top: 295px;
    margin: 0;
    font-size: 23px;
    font-weight: 700;
    color: var(--ink-dark);
    letter-spacing: 0.2px;
    white-space: nowrap;
  }
</style>
</head>
<body>
  <section class="card card--front" aria-label="Business card front">
    <div class="brand-mark">
      <span class="brand-mark__square"></span>
      <span class="brand-mark__text">BCS</span>
    </div>
  </section>

  <section class="card card--back" aria-label="Business card back">
    <p class="contact">
      <span class="contact__name">Liam Barlow</span>
      <span class="contact__line">M: liam_barlow@mailbox.com</span>
      <span class="contact__line">T: 0412580346</span>
      <span class="contact__line">ABN: 47 218 905 362</span>
    </p>
    <div class="brand-mark">
      <span class="brand-mark__square"></span>
      <span class="brand-mark__text">BCS</span>
    </div>
    <p class="company-name">BARLOW CONSTRUCTION SERVICES</p>
  </section>
</body>
</html>
```